Bright Harbor Painters Banner

Create a banner that displays and reinforces Bright Harbor Painters’ brand identity while promoting our interior painting services. The banner will be displayed at indoor venues through the winter. The design should be clean, professional, and visually recognizable to both new and returning customers. See attached design brief & logo source files.

```html
<!DOCTYPE html>
<html lang="en">
<head>
<meta charset="utf-8">
<title>Bright Harbor Painters Banner</title>
<link rel="stylesheet" href="https://fonts.googleapis.com/css2?family=Archivo:wdth,wght@125,700;125,800&family=Encode+Sans+Condensed:wght@600;700&display=swap">
<style>
  :root {
    --charcoal: #474747;
    --slate-text: #4a4a4a;
    --leaf: #6b9a4b;
    --paper: #ffffff;
    --backdrop: #e9ebee;
  }
  * { margin: 0; padding: 0; box-sizing: border-box; }
  html, body {
    width: 1200px;
    height: 879px;
    overflow: hidden;
    background: var(--backdrop);
  }
  .banner {
    position: absolute;
    left: 0;
    top: 257px;
    width: 1200px;
    height: 365px;
    overflow: hidden;
  }
  .banner-shapes {
    position: absolute;
    inset: 0;
  }
  .brand-name {
    position: absolute;
    left: 40px;
    top: 40px;
    width: 470px;
    font-family: "Archivo", Arial, sans-serif;
    font-stretch: 125%;
    font-weight: 800;
    font-size: 40px;
    line-height: 46px;
    color: var(--leaf);
    text-transform: uppercase;
    letter-spacing: 1px;
  }
  .tagline {
    position: absolute;
    left: 20px;
    top: 160px;
    width: 500px;
    text-align: center;
    font-family: "Archivo", Arial, sans-serif;
    font-stretch: 125%;
    font-weight: 700;
    color: var(--slate-text);
    font-size: 37px;
    line-height: 46px;
  }
  .service-heading {
    position: absolute;
    right: 28px;
    top: 20px;
    text-align: right;
    font-family: "Archivo", Arial, sans-serif;
    font-stretch: 125%;
    font-weight: 800;
    font-size: 56px;
    line-height: 54px;
    letter-spacing: 2px;
    color: var(--paper);
  }
  .service-list {
    position: absolute;
    right: 32px;
    top: 188px;
    text-align: right;
    font-family: "Archivo", Arial, sans-serif;
    font-stretch: 125%;
    font-weight: 700;
    font-size: 27px;
    line-height: 44px;
    color: var(--paper);
  }
  .call-to-action {
    position: absolute;
    left: 610px;
    right: 20px;
    top: 292px;
    text-align: center;
    font-family: "Encode Sans Condensed", "Arial Narrow", sans-serif;
    font-weight: 700;
    font-size: 27px;
    line-height: 35px;
    color: var(--paper);
  }
</style>
</head>
<body>
  <section class="banner" aria-label="Bright Harbor Painters interior painting services banner">
    <svg class="banner-shapes" width="1200" height="365" viewBox="0 0 1200 365" aria-hidden="true">
      <rect class="panel-dark" x="0" y="0" width="1200" height="365" fill="var(--charcoal)"/>
      <rect class="cta-band" x="0" y="285" width="1200" height="80" fill="var(--leaf)"/>
      <path class="divider-curve" d="M0 0 H525 C592 80 620 200 624 365 H0 Z" fill="var(--leaf)"/>
      <path class="panel-light" d="M0 0 H505 C572 80 600 200 604 365 H0 Z" fill="var(--paper)"/>
    </svg>

    <div class="brand-name">Bright Harbor<br>Painters</div>

    <p class="tagline">"Paint Smarter"<br>Trusted local<br>professionals,<br>since 2005</p>

    <h1 class="service-heading">INTERIOR<br>PAINTING<br>SERVICES</h1>

    <p class="service-list">Walls • Ceilings • Trim<br>• Cabinets • Drywall Repair</p>

    <p class="call-to-action">Call to action: Book a Free Estimate at<br>www.brightharborpainters.com</p>
  </section>
</body>
</html>
```